Direct to Consumer extended service contract business with a new disruptive business model needs a

We need a customized wordpress design for a company called 'Bright Harbor Assurance'.
We provide an innovative and unique service contract protection program direct to consumers. This program provides monthly coverage for all electronics purchased in the last 4 years and all electronics the consumer purchases in the future for a low monthly fee. The overall design should communicate a sense of legitimacy, ethics, and superior customer service and support (in an industry that has a huge PR issue to overcome).
Electronics is the first product group, other product groups with different price points to launch in the future..

Target Market(s)

All purchasers of electronic goods...all demographics

Industry/Entity Type

Electronics

Font styles to use
Sans Serif

Requirements
Must have
• Customer Testimonials
Industry News
Customer ratings
Blog posts
Call to action messaging
Like the functional elements and design of quillmesa.example (need to be better)
Nice to have
• Like to see video testimonials
Social network "whats trending related to electronics or service contract industry"
Easy way to register products for warranty

```html
<!DOCTYPE html>
<html lang="en">
<head>
<meta charset="utf-8">
<title>Bright Harbor Assurance</title>
<link href="https://fonts.googleapis.com/css2?family=Open+Sans:ital,wght@0,400;0,600;0,700;1,400&family=Roboto+Condensed:wght@400;700&display=swap" rel="stylesheet">
<style>
:root{
  --green:#3a9c3f;
  --green-dark:#2f8a35;
  --ink:#333;
  --muted:#8a8a8a;
  --panel:#4d4a48;
  --bar:#4a4a4a;
  --footer:#333333;
  --footer-deep:#292929;
  --star-red:#e2462f;
  --star-gold:#f2a71b;
  --line:#dcdcdc;
}
*{box-sizing:border-box;margin:0;padding:0}
html,body{width:822px;height:1200px;overflow:hidden;background:#fff}
body{position:relative;font-family:"Open Sans",sans-serif;color:var(--ink)}
.abs{position:absolute}
a{color:inherit;text-decoration:none}

/* top bar */
.topbar{left:0;top:0;width:822px;height:30px;background:var(--green)}
.topbar .phone{left:121px;top:9px;font-size:8px;color:#fff;letter-spacing:-.2px}
.topbar .phone span{color:#9be39e}
.topbar .social{top:10px;width:10px;height:10px;border-radius:50%;background:rgba(255,255,255,.85)}
.topbar .login{left:659px;top:8px;width:41px;height:17px;background:var(--green-dark);border:1px solid #2a7a2f;color:#fff;font-size:7px;text-align:center;line-height:15px}

/* header */
.header{left:0;top:30px;width:822px;height:71px;background:#fff;border-bottom:1px solid #e6e6e6}
.logo{left:120px;top:46px;color:var(--green);font-weight:700;font-size:19px;line-height:19px;letter-spacing:1.5px}
.logo small{display:block;font-size:19px;letter-spacing:1.5px}
.nav{top:62px;font-size:8.5px;color:#333;height:20px;line-height:20px}
.nav.active{background:var(--green);color:#fff;padding:0 11px;left:447px}

/* hero */
.hero{left:0;top:101px;width:822px;height:281px;background:linear-gradient(100deg,#f4f4f4 0%,#e4e4e4 40%,#f1f1f1 70%,#d9d9d9 100%)}
.hero-rule{left:0;top:382px;width:822px;height:3px;background:var(--green)}
.hero-panel{left:112px;top:101px;width:216px;height:177px;background:linear-gradient(180deg,#5a5654,#474341)}
.hero-title{left:133px;top:132px;width:186px;color:#fff;font-weight:700;font-size:24px;line-height:30px;letter-spacing:-.4px;white-space:nowrap}
.hero-sub{left:133px;top:203px;color:#fff;font-weight:700;font-size:8px;line-height:15px}
.hero-cta{left:112px;top:278px;width:216px;height:104px;background:var(--green)}
.hero-cta p{position:absolute;left:0;width:216px;top:29px;text-align:center;color:#fff;font-size:7px}
.hero-cta .btn{position:absolute;left:27px;top:46px;width:172px;height:28px;border:2px solid #fff;color:#fff;font-size:9px;letter-spacing:1.6px;text-align:center;line-height:24px}
.devices{left:345px;top:118px;width:355px;height:240px;background:linear-gradient(135deg,#fdfdfd 0%,#dfe3e6 45%,#1f2a30 70%,#0d1418 100%);border-radius:8px;opacity:.9}
.arrow{top:219px}

/* section headings */
.sec-title{font-size:11px;font-weight:600;color:#333}
.sec-title span{color:var(--green)}
.dotted{height:0;border-top:1px dotted #cfcfcf}
.bar-title{height:21px;background:var(--bar);color:#fff;font-family:"Roboto Condensed",sans-serif;font-weight:700;font-size:12px;line-height:21px;padding-left:7px;border-radius:2px}
.green-title{left:479px;top:407px;width:232px;height:21px;background:var(--green);color:#fff;font-family:"Roboto Condensed",sans-serif;font-weight:700;font-size:11px;line-height:21px;text-align:center;border-radius:2px}

/* testimonial video */
.video{left:116px;top:437px;width:324px;height:182px;background:#d8d8d8;padding:4px}
.video .frame{width:316px;height:174px;background:linear-gradient(90deg,#9a9490 0%,#b7aca2 45%,#7b7470 75%,#3b3a3a 100%)}
.testimonial-text{left:115px;top:632px;font-size:6.5px;color:var(--muted)}
.btn-small{background:var(--green);color:#fff;font-size:7px;text-align:center;border-radius:2px}

/* ratings */
.rating-name{font-size:9px;font-weight:600;color:#333}
.rating-meta{font-size:6.5px;color:var(--muted)}
.rating-link{font-size:7px;color:var(--green);font-weight:600}
.badge{background:#1e5f8f;border-radius:2px}
.badge2{background:#fff;border:1px solid #1e5f8f;border-radius:2px}

/* blog */
.thumb{width:82px;height:71px;border:1px solid #e3e3e3;padding:3px;background:#fff}
.thumb div{width:100%;height:100%}
.post-title{font-size:8px;color:var(--green);font-weight:600}
.post-body{font-size:6.2px;font-style:italic;color:#8d8d8d;line-height:11.5px;width:228px}
.post-meta{font-size:5.8px;color:#9a9a9a}
.sep{height:0;border-top:1px solid #e4e4e4}
.more{font-size:7.5px;color:var(--green);text-decoration:underline}

/* news */
.date{width:27px;height:31px;background:var(--green);color:#fff;font-size:7.5px;text-align:center;line-height:11px;padding-top:3px;border-bottom:2px solid #1f6e24}
.news-title{font-size:8.5px;color:#333;letter-spacing:.1px}
.news-body{font-size:6.6px;color:#8d8d8d;line-height:13.5px;width:165px}

/* footer */
.footer{left:0;top:998px;width:822px;height:174px;background:var(--footer)}
.footer-base{left:0;top:1172px;width:822px;height:28px;background:var(--footer-deep);border-top:1px solid #444}
.footer-base p{text-align:center;font-size:6px;color:#aaa;line-height:27px}
.f-head{font-size:8.5px;color:#fff}
.f-text{font-size:7.2px;color:#e6e6e6;line-height:13.5px}
.f-quote{font-size:7px;color:#cfcfcf;line-height:11px;width:138px}
.f-thumb{width:24px;height:22px;background:linear-gradient(180deg,#a7b59b,#6f7b63)}
.field{width:112px;height:17px;background:#6a6a6a;border-radius:2px;color:#eee;font-size:7px;line-height:17px;padding-left:6px}
.f-social{width:22px;height:22px;border-radius:50%;background:var(--green)}
</style>
</head>
<body>

<svg width="0" height="0" style="position:absolute">
  <defs>
    <symbol id="star" viewBox="0 0 20 19">
      <polygon points="10,0 12.9,6.3 20,7 14.6,11.8 16.2,19 10,15.2 3.8,19 5.4,11.8 0,7 7.1,6.3"/>
    </symbol>
    <symbol id="half" viewBox="0 0 20 19">
      <polygon points="10,0 10,15.2 3.8,19 5.4,11.8 0,7 7.1,6.3"/>
    </symbol>
  </defs>
</svg>

<!-- top bar -->
<div class="abs topbar">
  <div class="abs phone">855-555-HARBOR <span>(0142)</span></div>
  <div class="abs social" style="left:551px"></div>
  <div class="abs social" style="left:579px"></div>
  <div class="abs social" style="left:605px"></div>
  <div class="abs social" style="left:631px"></div>
  <div class="abs login">Login</div>
</div>

<!-- header -->
<header class="abs header"></header>
<div class="abs logo">BRIGHT HARBOR<small>ASSURANCE</small></div>
<nav>
  <a class="abs nav active">HOME</a>
  <a class="abs nav" style="left:509px">PLANS</a>
  <a class="abs nav" style="left:557px">BENEFITS</a>
  <a class="abs nav" style="left:615px">FAQS</a>
  <a class="abs nav" style="left:659px">ABOUT US</a>
</nav>

<!-- hero -->
<section class="abs hero"></section>
<div class="abs devices" role="img" aria-label="Laptop and smartphone showing the protection app"></div>
<svg class="abs" style="left:380px;top:188px" width="78" height="78" viewBox="0 0 78 78">
  <circle cx="39" cy="39" r="37" fill="none" stroke="#8d8d8d" stroke-width="3"/>
  <polygon points="31,23 31,55 57,39" fill="#8d8d8d"/>
</svg>
<svg class="abs arrow" style="left:72px" width="26" height="26" viewBox="0 0 26 26">
  <circle cx="13" cy="13" r="11.5" fill="#fff" fill-opacity=".6" stroke="#777" stroke-width="2"/>
  <polygon points="16,7 8,13 16,19" fill="#777"/>
</svg>
<svg class="abs arrow" style="left:720px" width="26" height="26" viewBox="0 0 26 26">
  <circle cx="13" cy="13" r="11.5" fill="#fff" fill-opacity=".6" stroke="#777" stroke-width="2"/>
  <polygon points="10,7 18,13 10,19" fill="#777"/>
</svg>
<div class="abs hero-panel"></div>
<h1 class="abs hero-title">BRIGHT HARBOR<br>ASSURANCE</h1>
<p class="abs hero-sub">THE DAYS OF BUYING EXPENSIVE<br>IN-STORE SERVICE PLANS ARE OVER!<br>BRIGHT HARBOR IS THE SOLUTION</p>
<div class="abs hero-cta">
  <p>GET YOUR BRIGHT HARBOR COVERAGE TODAY!</p>
  <a class="btn">CALL TO ACTION</a>
</div>
<div class="abs hero-rule"></div>

<!-- testimonials -->
<h2 class="abs sec-title" style="left:115px;top:410px">CUSTOMER <span>TESTIMONIALS</span></h2>
<div class="abs dotted" style="left:112px;top:429px;width:351px"></div>
<div class="abs video">
  <div class="frame" role="img" aria-label="Video testimonial from a customer in an office"></div>
</div>
<svg class="abs" style="left:264px;top:506px" width="42" height="42" viewBox="0 0 42 42">
  <circle cx="21" cy="21" r="19" fill="#fff" fill-opacity=".3" stroke="#eee" stroke-width="3"/>
  <polygon points="16,12 16,30 31,21" fill="#eee"/>
</svg>
<p class="abs testimonial-text">Sed ut perspiciatis iste natus error sit voluptatem accusantium doloremque laudantium.</p>
<a class="abs btn-small" style="left:391px;top:627px;width:50px;height:16px;line-height:16px">VIEW MORE</a>

<!-- ratings -->
<div class="abs green-title">RATED #1 BY THE PEOPLE WHO MATTER MOST</div>

<svg class="abs" style="left:489px;top:454px" width="88" height="17">
  <use href="#star" x="0" width="17" height="16" fill="var(--star-red)"/>
  <use href="#star" x="18" width="17" height="16" fill="var(--star-red)"/>
  <use href="#star" x="36" width="17" height="16" fill="var(--star-red)"/>
  <use href="#star" x="54" width="17" height="16" fill="var(--star-red)"/>
  <use href="#star" x="72" width="17" height="16" fill="#f1b3a8"/>
  <use href="#half" x="72" width="17" height="16" fill="var(--star-red)"/>
</svg>
<div class="abs rating-name" style="left:591px;top:446px">ORCHARD APP STORE</div>
<div class="abs rating-meta" style="left:591px;top:459px">4.5 AVERAGE ON 7000+ REVIEWS</div>
<div class="abs rating-link" style="left:591px;top:470px">READ THE REVIEWS &#9656;</div>

<svg class="abs" style="left:490px;top:502px" width="88" height="17">
  <use href="#star" x="0" width="17" height="16" fill="var(--star-gold)"/>
  <use href="#star" x="18" width="17" height="16" fill="var(--star-gold)"/>
  <use href="#star" x="36" width="17" height="16" fill="var(--star-gold)"/>
  <use href="#star" x="54" width="17" height="16" fill="var(--star-gold)"/>
  <use href="#star" x="72" width="17" height="16" fill="#f6d594"/>
  <use href="#half" x="72" width="17" height="16" fill="var(--star-gold)"/>
</svg>
<div class="abs rating-name" style="left:592px;top:494px">RIVERLINE MARKET</div>
<div class="abs rating-meta" style="left:592px;top:507px">4.5 AVERAGE ON 7000+ REVIEWS</div>
<div class="abs rating-link" style="left:591px;top:517px">READ THE REVIEWS &#9656;</div>

<svg class="abs" style="left:490px;top:553px" width="88" height="17">
  <use href="#star" x="0" width="17" height="16" fill="var(--star-red)"/>
  <use href="#star" x="18" width="17" height="16" fill="var(--star-red)"/>
  <use href="#star" x="36" width="17" height="16" fill="var(--star-red)"/>
  <use href="#star" x="54" width="17" height="16" fill="var(--star-red)"/>
  <use href="#star" x="72" width="17" height="16" fill="var(--star-red)"/>
</svg>
<div class="abs rating-name" style="left:592px;top:545px">SEARCHWISE</div>
<div class="abs rating-meta" style="left:590px;top:557px">4.5 AVERAGE ON 7000+ REVIEWS</div>
<div class="abs rating-link" style="left:590px;top:568px">READ THE REVIEWS &#9656;</div>

<div class="abs badge" style="left:490px;top:603px;width:58px;height:21px" role="img" aria-label="Trade bureau accreditation badge"></div>
<div class="abs badge2" style="left:551px;top:603px;width:30px;height:21px" role="img" aria-label="A+ rating badge"></div>
<div class="abs rating-meta" style="left:592px;top:597px;line-height:9.5px">TRADE BUREAU ACCREDITED WITH<br>AN A+ RATING</div>
<div class="abs rating-link" style="left:592px;top:618px">READ THE REVIEWS &#9656;</div>

<!-- recent blog posts -->
<h2 class="abs bar-title" style="left:112px;top:673px;width:343px">RECENT BLOG POSTS</h2>
<div class="abs dotted" style="left:112px;top:700px;width:351px"></div>

<div class="abs thumb" style="left:117px;top:718px"><div role="img" aria-label="Assorted household electronic gadgets" style="background:linear-gradient(135deg,#3b3b3b,#7d6fa8 45%,#2d2d2d)"></div></div>
<h3 class="abs post-title" style="left:216px;top:719px">The Average U.S. Household has about 40 Electric Gadgets</h3>
<p class="abs post-body" style="left:219px;top:734px">A wonderful serenity has taken possession of my entire soul, like these sweet mornings of spring which I enjoy with my whole heart. I am alone, and feel the charm of existence in this spot, which was created for the bliss of souls like mine. I am so happy, my dear that I neglect my talents.</p>
<div class="abs post-meta" style="left:222px;top:797px">&#9635; June 12 2014</div>
<div class="abs post-meta" style="left:290px;top:797px">&#9679; 2 Comments</div>
<div class="abs post-meta" style="left:357px;top:797px">&#9670; Admin</div>
<div class="abs post-meta" style="left:414px;top:797px">&#9829; 253</div>
<div class="abs sep" style="left:226px;top:813px;width:222px"></div>
<div class="abs sep" style="left:112px;top:826px;width:343px"></div>

<div class="abs thumb" style="left:117px;top:847px"><div role="img" aria-label="Smartphone lying on a surface" style="background:linear-gradient(135deg,#e8e8e8,#2b2b2b 55%,#9aa4ab)"></div></div>
<h3 class="abs post-title" style="left:216px;top:848px">The Average U.S. Household has about 40 Electric Gadgets</h3>
<p class="abs post-body" style="left:219px;top:863px">A wonderful serenity has taken possession of my entire soul, like these sweet mornings of spring which I enjoy with my whole heart. I am alone, and feel the charm of existence in this spot, which was created for the bliss of souls like mine. I am so happy, my dear that I neglect my talents.</p>
<div class="abs post-meta" style="left:222px;top:926px">&#9635; June 12 2014</div>
<div class="abs post-meta" style="left:290px;top:926px">&#9679; 2 Comments</div>
<div class="abs post-meta" style="left:357px;top:926px">&#9670; Admin</div>
<div class="abs post-meta" style="left:414px;top:926px">&#9829; 253</div>
<div class="abs sep" style="left:226px;top:940px;width:222px"></div>
<div class="abs sep" style="left:112px;top:950px;width:343px"></div>
<a class="abs more" style="left:423px;top:957px">more</a>

<!-- industry news -->
<h2 class="abs bar-title" style="left:479px;top:672px;width:232px;padding-left:17px">INDUSTRY NEWS</h2>
<div class="abs dotted" style="left:479px;top:700px;width:228px"></div>

<div class="abs date" style="left:495px;top:724px">22<br>AUG</div>
<div class="abs news-title" style="left:535px;top:724px">THE &nbsp;ABOUT 40 ELECTRIC GADGETS</div>
<p class="abs news-body" style="left:535px;top:738px">Donec viverra auctor lobortis. Pellentesque eu est a nulla placerat dignissim. Morbi a enim in magna semper bibendum. Etiam scelerisque,</p>
<div class="abs sep" style="left:495px;top:869px;width:211px"></div>

<div class="abs date" style="left:495px;top:802px">22<br>AUG</div>
<div class="abs news-title" style="left:535px;top:802px">THE &nbsp;ABOUT 40 ELECTRIC GADGETS</div>
<p class="abs news-body" style="left:535px;top:816px">Donec viverra auctor lobortis. Pellentesque eu est a nulla placerat dignissim. Morbi a enim in magna semper bibendum. Etiam scelerisque,</p>

<div class="abs date" style="left:495px;top:884px">22<br>AUG</div>
<div class="abs news-title" style="left:535px;top:884px">THE &nbsp;ABOUT 40 ELECTRIC GADGETS</div>
<p class="abs news-body" style="left:535px;top:898px">Donec viverra auctor lobortis. Pellentesque eu est a nulla placerat dignissim. Morbi a enim in magna semper bibendum. Etiam scelerisque,</p>
<div class="abs sep" style="left:495px;top:951px;width:211px"></div>
<a class="abs more" style="left:687px;top:956px">more</a>

<!-- footer -->
<footer class="abs footer"></footer>
<div class="abs f-head" style="left:112px;top:1012px">Social Network Feeds</div>
<div class="abs" style="left:115px;top:1034px;width:16px;height:16px;background:#3b5b98"></div>
<div class="abs" style="left:137px;top:1033px;font-size:7px;color:#ccc;font-weight:600">Get Fan Exclusives</div>
<div class="abs" style="left:137px;top:1043px;font-size:4.5px;color:#aaa">Follow our page &#9656;</div>
<div class="abs f-thumb" style="left:115px;top:1065px" role="img" aria-label="Feed thumbnail"></div>
<p class="abs f-quote" style="left:144px;top:1062px">"I received a $28,000 college scholarship, which made this class a phenomenal investment."</p>
<div class="abs f-thumb" style="left:115px;top:1101px" role="img" aria-label="Feed thumbnail"></div>
<p class="abs f-quote" style="left:144px;top:1099px">"I received a $28,000 college scholarship, which made this class a phenomena.</p>
<div class="abs f-thumb" style="left:115px;top:1134px" role="img" aria-label="Feed thumbnail"></div>
<p class="abs f-quote" style="left:144px;top:1131px">"I received a $28,000 college scholarship, which made this class a phenomena.</p>

<div class="abs f-head" style="left:299px;top:1012px">Contact</div>
<p class="abs f-text" style="left:299px;top:1032px;width:135px">Single ZIP city, unique first letter of single street name: 42 Linden Hollow Rd. Fairview ST 00000</p>
<div class="abs f-head" style="left:299px;top:1082px">Give us a Call</div>
<svg class="abs" style="left:299px;top:1096px" width="12" height="20" viewBox="0 0 12 20">
  <rect x="1" y="1" width="10" height="18" rx="2" fill="none" stroke="var(--green)" stroke-width="2"/>
  <rect x="4" y="15" width="4" height="1.5" fill="var(--green)"/>
</svg>
<p class="abs f-text" style="left:319px;top:1104px;font-size:6.5px">+1 (555) 010 22 31<br>+1 (555) 010 47 68</p>

<div class="abs f-head" style="left:441px;top:1012px">Weekly Newsletter</div>
<div class="abs field" style="left:440px;top:1038px">Name</div>
<div class="abs field" style="left:440px;top:1071px">Email</div>
<a class="abs btn-small" style="left:440px;top:1105px;width:47px;height:18px;line-height:18px;font-size:7.5px">Subscribe</a>

<div class="abs f-head" style="left:581px;top:1012px">Our products</div>
<p class="abs f-text" style="left:591px;top:1032px;line-height:13px">Product 1<br>Product 2<br>Product 2</p>
<div class="abs f-head" style="left:581px;top:1083px">Social Networks</div>
<div class="abs f-social" style="left:577px;top:1105px"></div>
<div class="abs f-social" style="left:605px;top:1105px"></div>
<div class="abs f-social" style="left:632px;top:1105px"></div>
<div class="abs f-social" style="left:659px;top:1105px"></div>

<div class="abs footer-base"><p>&copy; Copyright 2014 . www.brightharbor.example. All rights reserved.</p></div>

</body>
</html>
```